showcase project portfolio

create power point of project portfolio
from word file and website using similar design template

https://www.brelmor.co.uk/

Target Market(s)

corporte

```html
<!DOCTYPE html>
<html lang="en">
<head>
<meta charset="utf-8">
<title>Brelmor — Project Portfolio</title>
<link href="https://fonts.googleapis.com/css2?family=Poppins:wght@400;500;600;700&display=swap" rel="stylesheet">
<style>
  :root{
    --board:#9e9e9e;
    --paper:#ffffff;
    --ink:#0f3b4b;
    --body:#2f3b40;
    --tan:#c7a487;
    --rule:#dcc4ae;
    --navy:#1d3a54;
  }
  *{margin:0;padding:0;box-sizing:border-box}
  html,body{width:1079px;height:1200px;overflow:hidden;background:var(--board);font-family:"Poppins",sans-serif}
  .board{position:relative;width:1079px;height:1200px;background:var(--board)}
  .slide{position:absolute;width:420px;height:236px;background:var(--paper);overflow:hidden;box-shadow:0 6px 18px rgba(0,0,0,.35)}
  .col-l{left:114px}.col-r{left:546px}
  .row-1{top:107px}.row-2{top:357px}.row-3{top:607px}.row-4{top:857px}
  .abs{position:absolute}
  .slide-title{position:absolute;left:19px;top:13px;font-size:14px;font-weight:600;color:var(--ink);letter-spacing:.2px}
  .brand-tag{position:absolute;right:12px;top:14px;font-size:9px;font-weight:600;color:var(--ink);display:flex;align-items:center;gap:3px}
  .brand-tag i{width:6px;height:6px;border-radius:50%;background:var(--tan);display:block}
  .footer-rule{position:absolute;left:8px;right:20px;top:226px;height:1px;background:var(--rule)}
  .page-no{position:absolute;right:6px;top:221px;font-size:7px;font-weight:700;color:var(--ink)}
  .subtitle{position:absolute;left:19px;top:40px;font-size:8.5px;font-weight:600;color:var(--ink)}
  .proposal{position:absolute;left:19px;top:60px;font-size:6.3px;line-height:11px;color:var(--body)}
  .photo{position:absolute}
  .brick{background:linear-gradient(160deg,#8b5a45,#a86a52 50%,#6e4a3c)}
  .plan{background:linear-gradient(180deg,#f1f1ee,#e3e4df)}
  .plan-yellow{background:linear-gradient(180deg,#f4f2d6,#ecebd2 60%,#e8e8e4)}
  .greenery{background:linear-gradient(160deg,#5d6e4c,#3f4f36 60%,#7b7f78)}
  .task-list{position:absolute;list-style:none;font-size:6.3px;color:var(--body)}
  .task-list li{height:14px;line-height:14px;padding-left:9px;position:relative}
  .task-list li::before{content:"";position:absolute;left:0;top:5px;width:3px;height:3px;background:var(--tan)}
  /* cover */
  .cover-bg{position:absolute;inset:0;background:linear-gradient(110deg,#ebe6d7 0%,#f1eee3 45%,#f8f7f3 70%,#f3e9e4 100%)}
  .cover-brand{position:absolute;left:0;right:0;top:60px;text-align:center;font-size:34px;font-weight:600;color:var(--ink);letter-spacing:2px}
  .cover-sub{position:absolute;left:0;right:0;top:106px;text-align:center;font-size:8px;font-weight:500;color:var(--ink);letter-spacing:1px}
  .cover-line{position:absolute;left:0;right:0;top:178px;text-align:center;font-size:14.5px;font-weight:600;color:var(--ink)}
  /* closing */
  .closing{background:var(--navy)}
  .closing-bg{position:absolute;inset:0;background:linear-gradient(135deg,#243f58,#1b3650 55%,#203d57)}
  .closing-badge{position:absolute;left:151px;top:37px;width:116px;height:116px;border-radius:50%;background:#fff;border:5px solid var(--tan);display:flex;align-items:center;justify-content:center;font-size:17px;font-weight:600;color:var(--ink)}
  .closing-title{position:absolute;left:0;right:0;top:163px;text-align:center;font-size:23px;font-weight:700;color:#fff}
  .closing .footer-rule{background:#8aa0b3}
  .closing .page-no{color:#fff}
</style>
</head>
<body>
<main class="board">

  <!-- 01 cover -->
  <section class="slide col-l row-1">
    <div class="cover-bg" role="img" aria-label="Faded site plan with brick texture behind the title"></div>
    <div class="cover-brand">Brelmor</div>
    <div class="cover-sub">DESIGN STUDIO</div>
    <div class="cover-line">ARCHITECTURE TODAY,READY FOR TOMORROW</div>
    <div class="footer-rule"></div><div class="page-no">01</div>
  </section>

  <!-- 02 tasks -->
  <section class="slide col-l row-2">
    <h2 class="slide-title">TASKS</h2>
    <div class="brand-tag"><i></i>Brelmor</div>
    <ul class="task-list" style="left:19px;top:39px">
      <li>Creating working drawings</li>
      <li>Price breakdown of total build costs</li>
      <li>Liaising with Riverdale Water for water connection, drainage connection</li>
      <li>Liaising with Northline Gas to get gas supply to site</li>
      <li>Liaising with Grid Power Networks to get electric supply</li>
      <li>Tendering out works to different tradesman</li>
      <li>Getting material orders</li>
    </ul>
    <div class="photo brick" style="left:272px;top:33px;width:94px;height:65px" role="img" aria-label="Completed red brick detached house with lawn"></div>
    <div class="photo" style="left:20px;top:146px;width:140px;height:62px;background:linear-gradient(180deg,#a9c4de,#dfe6ea 55%,#8a8468)" role="img" aria-label="White rendered period building under blue sky"></div>
    <ul class="task-list" style="left:189px;top:114px">
      <li>Arranging structural engineer for the site</li>
      <li>Arranging Building control for the site</li>
      <li>Making sure material is on site on time</li>
      <li>Making sure all tradesman work is up to current British standards</li>
      <li>Daily walk rounds to check work is done according to approved plans</li>
      <li>Placing orders for bathrooms, kitchen, and flooring</li>
      <li>All snag work with main contactor</li>
    </ul>
    <div class="footer-rule"></div><div class="page-no">02</div>
  </section>

  <!-- 03 project one -->
  <section class="slide col-l row-3">
    <h2 class="slide-title">PROJECT ONE</h2>
    <div class="brand-tag"><i></i>Brelmor</div>
    <p class="subtitle">Garages at Linwood Mews, Linwood Street, Ashvale</p>
    <p class="proposal">Proposal: Change of use from garages to two dwelling houses (use class C3)<br>including alterations to the front and side elevations</p>
    <div class="photo brick" style="left:20px;top:92px;width:121px;height:120px" role="img" aria-label="Old brick garages with green timber doors"></div>
    <div class="photo plan-yellow" style="left:154px;top:92px;width:121px;height:120px" role="img" aria-label="Floor plans, section and elevations of the conversion"></div>
    <div class="photo brick" style="left:288px;top:44px;width:121px;height:168px" role="img" aria-label="Finished brick mews houses with dark front doors"></div>
    <div class="footer-rule"></div><div class="page-no">03</div>
  </section>

  <!-- 04 project two -->
  <section class="slide col-l row-4">
    <h2 class="slide-title">PROJECT TWO</h2>
    <div class="brand-tag"><i></i>Brelmor</div>
    <p class="subtitle">Location: 118 Marlow Road, Ashvale</p>
    <p class="proposal">Proposal: Change of use from offices (use class B1) to 12 flats (use class C3)</p>
    <div class="photo plan" style="left:20px;top:126px;width:125px;height:89px" role="img" aria-label="Floor plan drawings for the flats"></div>
    <div class="photo greenery" style="left:155px;top:92px;width:121px;height:117px" role="img" aria-label="Brick office building behind a large tree"></div>
    <div class="photo brick" style="left:289px;top:92px;width:121px;height:120px" role="img" aria-label="Front of the brick office building"></div>
    <div class="footer-rule"></div><div class="page-no">04</div>
  </section>

  <!-- 05 project three -->
  <section class="slide col-r row-1">
    <h2 class="slide-title">PROJECT THREE</h2>
    <div class="brand-tag"><i></i>Brelmor</div>
    <p class="subtitle">41-45 Quarry Lane Ashvale</p>
    <p class="proposal" style="width:380px">Proposal: Refurbishment Of Commercial Ground Floor Units Together With Formation Of 6 Residential Units On First And Second Floors. Installation Of Glazing And Repair To External Masonry Including Bricking Up Of Existing Openings</p>
    <div class="photo plan-yellow" style="left:23px;top:89px;width:335px;height:132px" role="img" aria-label="Ground, first and second floor plans showing six flats with fire safety legend"></div>
    <div class="footer-rule"></div><div class="page-no">05</div>
  </section>

  <!-- 06 project four -->
  <section class="slide col-r row-2">
    <h2 class="slide-title">PROJECT FOUR</h2>
    <div class="brand-tag"><i></i>Brelmor</div>
    <p class="subtitle">Land At 3 Fernhill Ashvale AV12 4QT</p>
    <p class="proposal">Proposal:&nbsp; Erection of a dwelling house (use class C3)</p>
    <div class="photo plan" style="left:276px;top:59px;width:126px;height:71px" role="img" aria-label="Floor plans and site plan of the new house"></div>
    <div class="photo greenery" style="left:18px;top:134px;width:126px;height:71px" role="img" aria-label="Overgrown vacant plot"></div>
    <div class="photo" style="left:148px;top:134px;width:126px;height:71px;background:linear-gradient(170deg,#6f7c58,#7a5a4c 55%,#5e5a58)" role="img" aria-label="Completed brick house with garage"></div>
    <div class="photo plan" style="left:276px;top:134px;width:126px;height:71px" role="img" aria-label="Proposed front elevation drawing"></div>
    <div class="footer-rule"></div><div class="page-no">06</div>
  </section>

  <!-- 07 project five -->
  <section class="slide col-r row-3">
    <h2 class="slide-title">PROJECT FIVE</h2>
    <div class="brand-tag"><i></i>Brelmor</div>
    <p class="subtitle">19, Corran Street, Westbridge</p>
    <p class="proposal">Proposal: Warehouse conversion to 4 town houses.</p>
    <div class="photo plan" style="left:212px;top:0;width:125px;height:71px" role="img" aria-label="Floor plans of the town houses"></div>
    <div class="photo brick" style="left:18px;top:74px;width:126px;height:146px" role="img" aria-label="Brick warehouse with arched windows and shutters"></div>
    <div class="photo brick" style="left:148px;top:74px;width:126px;height:146px" role="img" aria-label="Converted warehouse with rendered ground floor"></div>
    <div class="photo" style="left:277px;top:74px;width:126px;height:146px;background:linear-gradient(170deg,#6f98c8,#a2644f 40%,#6b6661)" role="img" aria-label="Rear courtyard of the brick warehouse"></div>
    <div class="footer-rule"></div><div class="page-no">07</div>
  </section>

  <!-- 08 thank you -->
  <section class="slide col-r row-4 closing">
    <div class="closing-bg" role="img" aria-label="Dark blue tinted street scene"></div>
    <div class="closing-badge">Brelmor</div>
    <div class="closing-title">THANK YOU</div>
    <div class="footer-rule"></div><div class="page-no">08</div>
  </section>

</main>
</body>
</html>
```